Professional & attention grabbing.

A business card design, front and back. I already have a logo I will attach, but I am open to something new as well.
Things to include:
Name:
Title:
Phone:
Email:
Wanting something that is professional but attention grabbing.
Also we do a lot of work using drones on natural gas pipelines (leading the future)if you want to include any of that. I'm open to ideas.
Target Market(s)
Natural gas transmission industry / greenhouse gas mitigation industry
Industry/Entity Type
Business
Colors
Designer to choose colors to be used in the design.
Look and feel
Each slider illustrates characteristics of the customer's brand and the style your logo design should communicate.

```html
<!DOCTYPE html>
<html lang="en">
<head>
<meta charset="utf-8">
<title>Kestrel Line Surveys – Business Card</title>
<link rel="stylesheet" href="https://fonts.googleapis.com/css2?family=Open+Sans:wght@400;600;700&display=swap">
<style>
  :root {
    --stage: #4a4a4a;
    --stage-top: #3c3c3c;
    --card-white: #ffffff;
    --brand-red: #c01f25;
    --brand-red-soft: #c8262c;
    --charcoal: #333336;
    --ink: #222222;
  }
  html, body {
    margin: 0;
    padding: 0;
    width: 1200px;
    height: 900px;
    overflow: hidden;
  }
  body {
    background: linear-gradient(180deg, var(--stage-top) 0%, var(--stage) 100%);
    font-family: "Open Sans", Arial, sans-serif;
    position: relative;
  }
  .card {
    position: absolute;
    top: 306px;
    width: 438px;
    height: 271px;
    overflow: hidden;
  }
  .card-front {
    left: 150px;
    background: var(--card-white);
  }
  .card-back {
    left: 608px;
    width: 441px;
    background: var(--brand-red);
  }
  .front-waves {
    position: absolute;
    inset: 0;
    width: 438px;
    height: 271px;
  }
  .brand {
    position: absolute;
    left: 21px;
    top: 38px;
    display: flex;
    align-items: center;
    gap: 9px;
  }
  .brand-square {
    width: 26px;
    height: 26px;
    background: var(--brand-red);
  }
  .brand-name {
    font-weight: 700;
    font-size: 19px;
    color: var(--charcoal);
    letter-spacing: 0.5px;
    line-height: 1;
  }
  .person {
    position: absolute;
    left: 22px;
    top: 133px;
  }
  .person-name {
    margin: 0;
    font-weight: 600;
    font-size: 15px;
    color: var(--brand-red);
    line-height: 18px;
  }
  .person-title {
    margin: 0;
    font-size: 12px;
    color: var(--ink);
    line-height: 16px;
  }
  .contacts {
    position: absolute;
    left: 288px;
    top: 135px;
    margin: 0;
    padding: 0;
    list-style: none;
    font-size: 12px;
    color: var(--ink);
  }
  .contacts li {
    display: flex;
    align-items: center;
    gap: 5px;
    line-height: 16px;
  }
  .contacts svg {
    width: 9px;
    height: 9px;
    fill: var(--brand-red);
  }
  .website {
    position: absolute;
    left: 22px;
    top: 232px;
    font-size: 12px;
    color: var(--card-white);
  }
  .back-pattern {
    position: absolute;
    inset: 0;
    background: var(--brand-red-soft);
  }
  .back-square {
    position: absolute;
    left: 152px;
    top: 67px;
    width: 137px;
    height: 137px;
    background: var(--card-white);
  }
  .back-name {
    position: absolute;
    left: 0;
    right: 0;
    top: 220px;
    text-align: center;
    font-weight: 700;
    font-size: 15px;
    letter-spacing: 1px;
    color: var(--card-white);
  }
</style>
</head>
<body>
  <section class="card card-front" aria-label="Business card front">
    <svg class="front-waves" viewBox="0 0 438 271" aria-hidden="true">
      <path d="M0,186 C110,180 200,198 270,226 C330,248 395,236 438,206 L438,271 L0,271 Z" fill="var(--brand-red)"/>
      <path d="M165,193 C235,203 300,226 360,216 C400,208 425,192 438,176 L438,192 C420,215 380,236 330,239 C270,242 220,214 165,193 Z" fill="var(--charcoal)"/>
    </svg>

    <div class="brand">
      <span class="brand-square"></span>
      <span class="brand-name">KESTREL LINE</span>
    </div>

    <div class="person">
      <p class="person-name">DANIEL PORTER</p>
      <p class="person-title">Managing Director</p>
    </div>

    <ul class="contacts">
      <li>
        <svg viewBox="0 0 10 10"><path d="M2,0.5 L3.6,2.6 L2.7,3.6 C3.3,5 4.9,6.7 6.4,7.3 L7.4,6.4 L9.5,8 L8.3,9.5 C4.5,9.2 0.8,5.5 0.5,1.7 Z"/></svg>
        <span>(044)987650321</span>
      </li>
      <li>
        <svg viewBox="0 0 10 10"><path d="M0,2 L10,2 L10,8.5 L0,8.5 Z M0.8,2.6 L5,5.6 L9.2,2.6" /><path d="M0.8,2.6 L5,5.6 L9.2,2.6" stroke="#fff" stroke-width="0.9" fill="none"/></svg>
        <span>info@kestrelline.com</span>
      </li>
    </ul>

    <span class="website">www.kestrelline.com</span>
  </section>

  <section class="card card-back" aria-label="Business card back">
    <div class="back-pattern" role="img" aria-label="Subtle repeating brand pattern in tonal red"></div>
    <div class="back-square"></div>
    <div class="back-name">KESTREL LINE</div>
  </section>
</body>
</html>
```